Business card for Luxury Portable Restroom Trailer company

We are a Luxury Portable Restroom Trailer Company Called FALCRIDGE HIRES. Based in Orange County California. We provide portable restroom trailers for events, such as, Weddings, Concerts, Charity events, Sporting events, Tournaments, Corporate events, ect. We rent and Sell the Luxury restrooms. Our colors are white, grey, and Orange. As you will see in the logo we uploaded.
There are 2 people in the company so the names and titles will change for the 3 people but card will remain the same. Here is the information for each Person: Dwight Penner CFO 555 318-0476
next Person: Leon Marchetti VP 555 318-0476
Next Person: Owen Marchetti CEO 555 318-0476
Information to include on the card: Luxury Restroom Trailers Rental and Sales. Weddings, Concerts, Charity, Sporting and Corp. Events.

```html
<!DOCTYPE html>
<html lang="en">
<head>
<meta charset="utf-8">
<title>FALCRIDGE HIRES — Business Card</title>
<link href="https://fonts.googleapis.com/css2?family=Montserrat:wght@400;500;700;800&display=swap" rel="stylesheet">
<style>
  :root {
    --backdrop: #1b1c1f;
    --card: #141416;
    --card-edge: #f2661f;
    --accent: #f2661f;
    --text-light: #e9e9ea;
    --text-muted: #a9a9ad;
    --ghost: #202023;
  }
  * { box-sizing: border-box; margin: 0; padding: 0; }
  html, body {
    width: 1200px; height: 900px; overflow: hidden;
    background: var(--backdrop);
    font-family: "Montserrat", sans-serif;
  }
  .stage { position: relative; width: 1200px; height: 900px; }
  .card {
    position: absolute; left: 270px;
    width: 660px; height: 377px;
    background: var(--card);
    border-radius: 22px;
    border-bottom: 4px solid var(--card-edge);
    border-left: 2px solid var(--card-edge);
    box-shadow: 0 18px 40px rgba(0,0,0,0.45);
    overflow: hidden;
  }
  .card--back { top: 55px; }
  .card--front { top: 468px; }

  .ghost-name {
    position: absolute;
    color: var(--ghost);
    font-weight: 800;
    letter-spacing: 0.02em;
    white-space: nowrap;
  }
  .card--back .ghost-name {
    left: 50%; top: 50%; transform: translate(-50%, -50%);
    font-size: 62px;
  }
  .card--front .ghost-name {
    right: 38px; top: 178px;
    font-size: 28px;
  }

  .brand {
    position: absolute; left: 40px; top: 38px;
    display: flex; align-items: center; gap: 10px;
  }
  .brand__mark { width: 16px; height: 16px; background: var(--accent); }
  .brand__name {
    color: var(--accent); font-weight: 800; font-size: 26px; letter-spacing: 0.02em;
  }

  .person { position: absolute; left: 40px; top: 118px; }
  .person__name { color: var(--accent); font-weight: 700; font-size: 30px; }
  .person__title { color: var(--text-light); font-weight: 400; font-size: 17px; margin-top: 2px; }

  .address {
    position: absolute; left: 40px; top: 195px;
    color: var(--text-light); font-size: 15px; line-height: 1.35;
  }

  .contacts {
    position: absolute; left: 40px; top: 255px;
    list-style: none;
    color: var(--text-light); font-size: 15px; line-height: 1.5;
  }
  .contacts li { display: flex; align-items: center; gap: 10px; }
  .contacts svg { width: 13px; height: 13px; fill: var(--accent); flex: none; }

  .tagline {
    position: absolute; right: 38px; bottom: 34px;
    width: 300px; text-align: right;
    color: var(--text-muted); font-size: 12px; line-height: 1.5;
  }
  .tagline__lead { color: var(--accent); font-weight: 700; }
</style>
</head>
<body>
<main class="stage">

  <section class="card card--back" aria-label="Card back">
    <span class="ghost-name">FALCRIDGE HIRES</span>
  </section>

  <section class="card card--front" aria-label="Card front">
    <div class="brand">
      <span class="brand__mark"></span>
      <span class="brand__name">FALCRIDGE HIRES</span>
    </div>

    <div class="person">
      <p class="person__name">Owen Marchetti</p>
      <p class="person__title">CEO</p>
    </div>

    <p class="address">418 Harbor View Dr, #112<br>Tustin, CA 92780</p>

    <ul class="contacts">
      <li>
        <svg viewBox="0 0 16 16" aria-hidden="true"><path d="M3 1h3l1.5 4-2 1.2a9 9 0 0 0 4.3 4.3L11 8.5l4 1.5v3a2 2 0 0 1-2 2A12 12 0 0 1 1 3a2 2 0 0 1 2-2z"/></svg>
        555 318-0476
      </li>
      <li>
        <svg viewBox="0 0 16 16" aria-hidden="true"><path d="M4 0h8a1 1 0 0 1 1 1v14a1 1 0 0 1-1 1H4a1 1 0 0 1-1-1V1a1 1 0 0 1 1-1zm1 2v10h6V2zm3 11a1 1 0 1 0 0 2 1 1 0 0 0 0-2z"/></svg>
        555 318-0476
      </li>
      <li>
        <svg viewBox="0 0 16 16" aria-hidden="true"><path d="M0 3h16v10H0zm1.5 1.2v.3L8 9l6.5-4.5v-.3z"/></svg>
        info@falcridgehires.com
      </li>
      <li>
        <svg viewBox="0 0 16 16" aria-hidden="true"><path d="M8 0a8 8 0 1 0 0 16A8 8 0 0 0 8 0zm0 1.5c1 0 2 2 2.3 5.5H5.7C6 3.5 7 1.5 8 1.5zM5.7 9h4.6C10 12.5 9 14.5 8 14.5S6 12.5 5.7 9z"/></svg>
        www.falcridgehires.com
      </li>
    </ul>

    <span class="ghost-name">FALCRIDGE HIRES</span>

    <p class="tagline">
      <span class="tagline__lead">Luxury Restroom Trailers Rental and Sales.</span><br>
      Weddings, Concerts, Charity, Sporting and Corp. Events.
    </p>
  </section>

</main>
</body>
</html>
```